Business Card Design & Gift cards, Gift Cert, Donation Card

Retail Gift Store-in addition to Business Cards we'd like sequenced 2 sided Gift cards, Gift Certificate Cards, and Donation Cards.please see examples and email for clarificationlogos attached with examples-
Gift Card, Gift Certificate and Donation Card will all be same style just differant upper right title, with back side info as example.
business card, as example is single sided.
looking for additional ideas for layout

Industry/Entity Type

Business

Contact Information for Business Card

482 Larkfield Ave..East Tawas, MI 48730989.362.8730Office@BrewKrew.com

Requirements
Must have
• Blue as per example
• Logos provided
• like gradiant background

```html
<!DOCTYPE html>
<html lang="en">
<head>
<meta charset="utf-8">
<title>Tillow Marsh – Business Card</title>
<link href="https://fonts.googleapis.com/css2?family=Kalam:wght@400&display=swap" rel="stylesheet">
<style>
  :root {
    --page-bg: #e9eaec;
    --sky-top: #88c4f3;
    --sky-mid: #bcdcf6;
    --sky-bottom: #f6f9fd;
    --ink-blue: #1434c8;
    --ink-dark: #111418;
    --sun-yellow: #f5e20a;
  }
  * { margin: 0; padding: 0; box-sizing: border-box; }
  html, body {
    width: 1189px;
    height: 1200px;
    overflow: hidden;
    background: var(--page-bg);
    font-family: "Kalam", cursive;
  }
  .card {
    position: absolute;
    left: 140px;
    width: 917px;
    height: 521px;
    background: linear-gradient(to bottom, var(--sky-top) 0%, var(--sky-mid) 45%, var(--sky-bottom) 100%);
    overflow: hidden;
  }
  .card--front { top: 47px; }
  .card--back { top: 624px; }

  .brand-name {
    position: absolute;
    color: var(--ink-blue);
    font-weight: 400;
    white-space: nowrap;
    line-height: 1;
  }
  .card--front .brand-name {
    left: 70px;
    top: 56px;
    font-size: 64px;
  }
  .card--back .brand-name {
    left: 84px;
    top: 196px;
    font-size: 146px;
  }

  .illustration {
    position: absolute;
  }
  .card--front .illustration {
    left: 52px;
    top: 150px;
    width: 330px;
    height: 342px;
  }
  .card--back .illustration {
    left: 6px;
    top: 18px;
    width: 468px;
    height: 496px;
    opacity: 0.35;
  }

  .contact {
    position: absolute;
    right: 79px;
    top: 332px;
    text-align: right;
    color: var(--ink-dark);
    font-size: 25px;
    font-style: normal;
    line-height: 37px;
    letter-spacing: 0.5px;
  }
</style>
</head>
<body>
  <section class="card card--front">
    <div class="brand-name">Tillow Marsh</div>
    <svg class="illustration" role="img" aria-label="Mascot illustration: dancing figure stepping on a rising sun over a hill" viewBox="0 0 330 342" preserveAspectRatio="none">
      <defs>
        <linearGradient id="frontArt" x1="0" y1="0" x2="0" y2="1">
          <stop offset="0" stop-color="#1434c8" stop-opacity="0.55"/>
          <stop offset="0.7" stop-color="#1434c8" stop-opacity="0.35"/>
          <stop offset="1" stop-color="#f5e20a" stop-opacity="0.6"/>
        </linearGradient>
      </defs>
      <rect width="330" height="342" rx="18" fill="url(#frontArt)"/>
    </svg>
    <address class="contact">
      482 Larkfield Ave.<br>
      Harlow Bend, MI 49215<br>
      989.517.4296<br>
      Office@TillowMarsh.com
    </address>
  </section>

  <section class="card card--back">
    <svg class="illustration" role="img" aria-label="Faint background mascot illustration: dancing figure on a rising sun" viewBox="0 0 468 496" preserveAspectRatio="none">
      <defs>
        <linearGradient id="backArt" x1="0" y1="0" x2="0" y2="1">
          <stop offset="0" stop-color="#6f9ae8"/>
          <stop offset="0.7" stop-color="#9db7ee"/>
          <stop offset="1" stop-color="#eef0b0"/>
        </linearGradient>
      </defs>
      <rect width="468" height="496" rx="24" fill="url(#backArt)"/>
    </svg>
    <div class="brand-name">Tillow Marsh</div>
  </section>
</body>
</html>
```